Brightbay Orthodontics business card design

Need a business card design that reflects our re-branding (orthodontic office - braces) and a new partnership with a pediatric dental office. We would like to include "for adults and children" on the card as well so adults know they are welcome to get their braces here as well. Office design is modern and would like business card to reflect a modern type look. Here's the text we would like to be included on the card:

Darren Wolcott, DDS, MSD
5214 West Linden Avenue, Suite 204
Cedar Hollow, OR 76991
555-418-2637
www.brightbayortho.example
info@brightbayortho.example

Can we add the following to the existing designs? Darren Wolcott, DDS, MSD 5214 West Linden Avenue, Suite 204 Cedar Hollow, OR 76991 555-418-2637

Does anyone have any more vertical designs available? Thanks!

Dental

```html
<!DOCTYPE html>
<html lang="en">
<head>
<meta charset="utf-8">
<title>Brightbay Orthodontics — Business Card</title>
<link rel="stylesheet" href="https://fonts.googleapis.com/css2?family=Open+Sans:wght@400;600;700&display=swap">
<style>
  :root {
    --backdrop: #3b3b3b;
    --card: #ffffff;
    --ink: #222222;
    --ink-soft: #333333;
    --magenta: #e5127d;
    --black: #231f20;
    --yellow: #fff200;
    --blue: #1b75bb;
    --green: #8dc63f;
    --orange: #f7941d;
    --icon-green: #39b54a;
  }
  * { margin: 0; padding: 0; box-sizing: border-box; }
  html, body {
    width: 1200px; height: 900px; overflow: hidden;
    background: var(--backdrop);
    font-family: "Open Sans", Arial, sans-serif;
  }
  .canvas { position: relative; width: 1200px; height: 900px; }
  .card {
    position: absolute; top: 135px; width: 354px; height: 637px;
    background: var(--card); overflow: hidden;
  }
  .card-front { left: 245px; }
  .card-back { left: 625px; }

  .wordmark {
    position: absolute; left: 0; right: 0; text-align: center;
    color: var(--ink); font-weight: 700; line-height: 1.05;
  }
  .wordmark-dot {
    display: inline-block; border-radius: 50%; background: var(--magenta);
    vertical-align: middle;
  }
  .card-front .wordmark { top: 228px; font-size: 40px; }
  .card-front .wordmark-dot { width: 22px; height: 22px; margin-right: 10px; }
  .card-front .wordmark-sub { display: block; font-size: 30px; margin-top: 6px; }
  .card-back .wordmark { top: 46px; font-size: 30px; }
  .card-back .wordmark-dot { width: 16px; height: 16px; margin-right: 8px; }
  .card-back .wordmark-sub { display: block; font-size: 21px; margin-top: 4px; }

  .audience-band {
    position: absolute; height: 42px; color: #fff;
    font-size: 18px; letter-spacing: 1px; line-height: 42px;
  }
  .audience-children { left: 0; top: 526px; width: 266px; background: var(--magenta); padding-left: 102px; }
  .audience-adults { left: 78px; top: 571px; width: 276px; background: var(--black); padding-left: 26px; }

  .colour-strip { position: absolute; left: 0; top: 423px; width: 22px; }
  .colour-strip span { display: block; width: 22px; }
  .strip-yellow { height: 44px; background: var(--yellow); }
  .strip-blue { height: 45px; background: var(--blue); }
  .strip-magenta { height: 44px; background: var(--magenta); }
  .strip-green { height: 45px; background: var(--green); }
  .strip-orange { height: 17px; background: var(--orange); }

  .doctor-name {
    position: absolute; left: 53px; top: 420px;
    font-size: 18px; font-weight: 700; letter-spacing: 1px; color: var(--ink);
  }
  .address {
    position: absolute; left: 53px; top: 484px;
    font-size: 14px; line-height: 22px; color: var(--ink-soft); letter-spacing: 0.3px;
  }
  .contact-list { position: absolute; left: 53px; top: 539px; list-style: none; }
  .contact-list li {
    display: flex; align-items: center; height: 24px;
    font-size: 14px; color: var(--ink-soft); letter-spacing: 0.3px;
  }
  .contact-icon { width: 14px; height: 14px; margin-right: 26px; flex: none; }
</style>
</head>
<body>
<main class="canvas">
  <section class="card card-front" aria-label="Card front">
    <div class="wordmark">
      <span class="wordmark-dot"></span>Brightbay
      <span class="wordmark-sub">Orthodontics</span>
    </div>
    <div class="audience-band audience-children">FOR CHILDREN</div>
    <div class="audience-band audience-adults">AND ADULTS</div>
  </section>

  <section class="card card-back" aria-label="Card back">
    <div class="wordmark">
      <span class="wordmark-dot"></span>Brightbay
      <span class="wordmark-sub">Orthodontics</span>
    </div>

    <div class="colour-strip" aria-hidden="true">
      <span class="strip-yellow"></span>
      <span class="strip-blue"></span>
      <span class="strip-magenta"></span>
      <span class="strip-green"></span>
      <span class="strip-orange"></span>
    </div>

    <h1 class="doctor-name">Darren Wolcott, DDS, MSD</h1>
    <p class="address">5214 West Linden Avenue, Suite 204<br>Cedar Hollow, OR 76991</p>

    <ul class="contact-list">
      <li>
        <svg class="contact-icon" viewBox="0 0 16 16" aria-hidden="true">
          <path d="M2 5c0-2 2-3 6-3s6 1 6 3v1h-3V5H5v1H2z" fill="var(--icon-green)"/>
          <rect x="3" y="7" width="10" height="7" rx="1" fill="none" stroke="var(--icon-green)" stroke-width="1.5"/>
          <circle cx="8" cy="10.5" r="1.6" fill="var(--icon-green)"/>
        </svg>555-418-2637
      </li>
      <li>
        <svg class="contact-icon" viewBox="0 0 16 16" aria-hidden="true">
          <rect x="1.5" y="3.5" width="13" height="9" fill="none" stroke="var(--icon-green)" stroke-width="1.5"/>
          <path d="M1.5 3.5 8 9l6.5-5.5" fill="none" stroke="var(--icon-green)" stroke-width="1.5"/>
        </svg>info@brightbayortho.example
      </li>
      <li>
        <svg class="contact-icon" viewBox="0 0 16 16" aria-hidden="true">
          <circle cx="8" cy="8" r="6.3" fill="none" stroke="var(--icon-green)" stroke-width="1.5"/>
          <ellipse cx="8" cy="8" rx="2.6" ry="6.3" fill="none" stroke="var(--icon-green)" stroke-width="1.2"/>
          <path d="M1.7 8h12.6" stroke="var(--icon-green)" stroke-width="1.2"/>
        </svg>www.brightbayortho.example
      </li>
    </ul>
  </section>
</main>
</body>
</html>
```